Brightway Carpet and Tile cleaning Business card Design

I need a design that has the same feel as my van.
i would also like a prominent "Review us on friendnest" somewhere, but not that it makes it look silly.
I would like the card to have a little bit of grey or black in the design as well.

It will need contact details
phone: 0455 817264
email: rkbrightwayclean@mailbox-example.com
website: www.brightwaycarpetandtilecleaning-example.com.au
friendnest: /brightwaycarpetandtilecleaning

Industry/Entity Type

Business

Contact Information for Business Card

Phone number 0455817264
Email rkbrightwayclean@mailbox-example.com
Website www.brightwaycarpetandtilecleaning-example.com.au
Facebook/brightwaycarpetandtilecleaning

Colors
000000

Requirements
Must have
• Same feel as my van
• I want the card to stand out from the crowd
Nice to have
• Maybe include a tiny bit of a third colour? Grey's,blacks, orange?

```html
<!DOCTYPE html>
<html lang="en">
<head>
<meta charset="utf-8">
<title>Brightway Carpet and Tile cleaning – Business Card</title>
<link href="https://fonts.googleapis.com/css2?family=Roboto:wght@300;400;500&display=swap" rel="stylesheet">
<style>
  :root {
    --backdrop: #bdbdbd;
    --card: #ffffff;
    --shadow: #8c8c8c;
    --brand-blue: #29abe2;
    --charcoal: #5a5a5a;
    --ink: #333333;
    --soft-ink: #666666;
  }
  * { margin: 0; padding: 0; box-sizing: border-box; }
  html, body {
    width: 1200px; height: 1200px; overflow: hidden;
    background: var(--backdrop);
    font-family: "Roboto", Arial, sans-serif;
  }
  .stage { position: relative; width: 1200px; height: 1200px; }
  .card {
    position: absolute; top: 197px; width: 429px; height: 702px;
    background: var(--card);
    box-shadow: 14px 14px 8px var(--shadow);
    overflow: hidden;
  }
  .card--front { left: 121px; }
  .card--back { left: 610px; }

  .brand {
    position: absolute; left: 0; width: 100%;
    display: flex; align-items: center; justify-content: center; gap: 12px;
    color: var(--brand-blue); font-weight: 500;
    text-align: center; line-height: 1.1;
  }
  .brand__dot {
    width: 26px; height: 26px; border-radius: 50%;
    background: var(--brand-blue); flex: none;
  }
  .brand__name { font-size: 34px; }
  .brand__name small { display: block; font-size: 15px; letter-spacing: 2px; margin-top: 6px; }
  .card--front .brand { top: 312px; }
  .card--back .brand { top: 120px; }

  .social-mark {
    position: absolute; left: 202px; top: 602px;
    width: 24px; height: 24px; border: 2px solid var(--brand-blue);
  }
  .handle {
    position: absolute; left: 0; width: 100%; text-align: center;
    font-weight: 300; font-size: 21px; color: var(--soft-ink);
  }
  .card--front .handle { top: 636px; }

  .divider-bar {
    position: absolute; left: 54px; top: 243px; width: 322px; height: 16px;
  }
  .contact {
    position: absolute; left: 0; width: 100%; text-align: center;
    font-weight: 400; color: var(--ink); font-size: 19px;
  }
  .contact--phone { top: 346px; }
  .contact--email { top: 439px; }
  .contact--web { top: 533px; font-size: 15px; }
  .rule {
    position: absolute; left: 59px; width: 312px; height: 2px;
    background: var(--brand-blue);
  }
  .rule--one { top: 401px; }
  .rule--two { top: 496px; }

  .review-band {
    position: absolute; left: 0; top: 599px; width: 100%; height: 31px;
    background: var(--charcoal); color: var(--brand-blue);
    font-size: 19px; font-weight: 300; text-align: center; line-height: 31px;
  }
  .card--back .handle { top: 637px; font-weight: 400; font-size: 19px; color: var(--ink); }
</style>
</head>
<body>
<main class="stage">
  <section class="card card--front">
    <div class="brand">
      <span class="brand__dot"></span>
      <span class="brand__name">Brightway<small>CARPET &amp; TILE CLEANING</small></span>
    </div>
    <span class="social-mark" aria-hidden="true"></span>
    <p class="handle">brightwaycarpetandtilecleaning</p>
  </section>

  <section class="card card--back">
    <div class="brand">
      <span class="brand__dot"></span>
      <span class="brand__name">Brightway<small>CARPET &amp; TILE CLEANING</small></span>
    </div>
    <svg class="divider-bar" viewBox="0 0 322 16" aria-hidden="true">
      <polygon points="8,0 314,0 322,16 0,16" fill="var(--charcoal)"/>
    </svg>
    <p class="contact contact--phone">0455 817264</p>
    <span class="rule rule--one"></span>
    <p class="contact contact--email">rkbrightwayclean@mailbox-example.com</p>
    <span class="rule rule--two"></span>
    <p class="contact contact--web">www.brightwaycarpetandtilecleaning-example.com.au</p>
    <div class="review-band">Review us on friendnest</div>
    <p class="handle">brightwaycarpetandtilecleaning</p>
  </section>
</main>
</body>
</html>
```